Grafic Ad for a Printmagazine about Tractor Vehicles

We need for a Geman Printmagazine about Tractors a Grafic Design in different sizes. Our Website and corporate Design: https://www.kalvimo.de You can work with the uploaded files . The round Logo with shaking hands should be included in your Designs somehow. Perhaps as a transparent in the background or placed in a corner. The Font used for the URL is Days (typelodge.com/days.font) Please use this Font or a other similar for the URL "kalvimo.de" and expand it to "www.kalvimo.de/traktorwert" For the other Text parts (first line) and (second line) you can use a other font which you prefer. We need the grafics as .jpg in the pixel sizes: 472x496, 437x614, 307x437 (Print would be DPI 300). Goal is a eye-catching design for the later print ad. Have fun and be creative ;)

Logo Text

"Traktor Bewertung" (first line), " Kurzgutachen für Verkauf, Kauf oder Versicherung" (second line), "www.kalvimo.de/traktorwert" (third line)

Logo styles of interest
Pictorial/Combination Logo
Font styles to use
Other font styles liked:
• Days.tff for the URL

Colors
0054AA
0677BA
7BADD7
CADEEF
E8F1F8
0094D4
00A9DD
6FCCEA
C7EBF8
E9F6FB

```html
<!DOCTYPE html>
<html lang="de">
<head>
<meta charset="utf-8">
<title>Traktor Bewertung – Anzeigen</title>
<link href="https://fonts.googleapis.com/css2?family=Days+One&display=swap" rel="stylesheet">
<style>
  :root{
    --page:#e8e8e8;
    --white:#ffffff;
    --ink:#4a4a4a;
    --brand:#0677BA;
    --brand-deep:#0054AA;
    --blue-top:#1d7ec3;
    --blue-mid:#4a9fd8;
    --blue-low:#8fd3f2;
    --swoosh:#7BADD7;
    --swoosh-light:#C7EBF8;
    --star-light:#9fd0f0;
    --star-dark:#2a86cc;
    --photo-a:#7fa9cf;
    --photo-b:#3f6f9c;
  }
  *{box-sizing:border-box;margin:0;padding:0}
  html,body{width:1200px;height:2371px;overflow:hidden}
  body{background:var(--page);position:relative;font-family:"Days One",sans-serif}

  .ad{position:absolute;overflow:hidden;background:var(--white)}
  .ad-wide{left:96px;top:94px;width:990px;height:705px}
  .ad-tall{left:192px;top:882px;width:800px;height:760px}
  .ad-small{left:239px;top:1734px;width:706px;height:494px}

  .ad .backdrop{position:absolute;inset:0;width:100%;height:100%}
  .ad > *{position:absolute}

  .brand{display:flex;flex-direction:column;align-items:center;gap:10px}
  .brand-dot{border-radius:50%;background:var(--swoosh-light)}
  .brand-name{color:var(--brand);font-family:"Days One",sans-serif;white-space:nowrap}

  .stars{overflow:visible}

  .headline{white-space:nowrap;color:var(--ink);letter-spacing:.5px}
  .headline .accent{color:var(--brand)}

  .tractor-photo{border-radius:8px;background:radial-gradient(ellipse at 50% 45%,var(--photo-a) 0%,var(--photo-b) 60%,rgba(63,111,156,0) 72%)}

  .services{color:var(--white);text-shadow:0 2px 3px rgba(0,40,90,.55)}
  .services .lead{display:block}
  .service{display:flex;align-items:center}
  .service svg{flex:none;fill:none;stroke:var(--white);stroke-width:2;stroke-linejoin:round;stroke-linecap:round}

  .url-pill{display:flex;align-items:center;justify-content:center;border-radius:999px;
    background:linear-gradient(180deg,#4aa6e2 0%,#1a72bb 55%,#2d8fd3 100%);
    border:3px solid var(--white);box-shadow:0 8px 12px rgba(0,50,110,.35);
    color:var(--white);white-space:nowrap;text-shadow:0 2px 4px rgba(0,30,80,.6)}

  /* wide */
  .ad-wide .brand{left:50px;top:34px;width:200px}
  .ad-wide .brand-dot{width:96px;height:96px}
  .ad-wide .brand-name{font-size:25px}
  .ad-wide .stars{left:504px;top:16px;width:360px;height:108px}
  .ad-wide .headline{left:444px;top:128px;font-size:46px}
  .ad-wide .tractor-photo{left:156px;top:278px;width:336px;height:258px}
  .ad-wide .services{left:652px;top:246px;width:320px}
  .ad-wide .services .lead{font-size:22px;margin-bottom:28px}
  .ad-wide .service{font-size:23px;gap:18px;height:94px;margin-left:20px}
  .ad-wide .service svg{width:40px;height:44px}
  .ad-wide .url-pill{left:52px;top:566px;width:880px;height:88px;font-size:48px}

  /* tall */
  .ad-tall .brand{left:22px;top:40px;width:200px}
  .ad-tall .brand-dot{width:96px;height:96px}
  .ad-tall .brand-name{font-size:27px}
  .ad-tall .stars{left:336px;top:32px;width:360px;height:108px}
  .ad-tall .headline{left:280px;top:148px;font-size:46px}
  .ad-tall .tractor-photo{left:90px;top:330px;width:366px;height:282px}
  .ad-tall .services{left:500px;top:278px;width:244px;text-align:center}
  .ad-tall .services .lead{font-size:20px;margin-bottom:22px}
  .ad-tall .service{flex-direction:column;font-size:26px;gap:6px;margin-bottom:10px}
  .ad-tall .service svg{width:48px;height:48px}
  .ad-tall .url-pill{left:46px;top:650px;width:696px;height:68px;font-size:40px}

  /* small */
  .ad-small .brand{left:36px;top:20px;width:130px;gap:6px}
  .ad-small .brand-dot{width:68px;height:68px}
  .ad-small .brand-name{font-size:19px}
  .ad-small .stars{left:372px;top:12px;width:236px;height:72px}
  .ad-small .headline{left:335px;top:90px;font-size:30px}
  .ad-small .tractor-photo{left:91px;top:192px;width:255px;height:198px}
  .ad-small .services{left:431px;top:164px;width:260px}
  .ad-small .services .lead{font-size:17px;margin-bottom:22px}
  .ad-small .service{font-size:17px;gap:14px;height:70px;margin-left:14px;margin-top:-16px;margin-bottom:16px}
  .ad-small .service svg{width:30px;height:34px}
  .ad-small .url-pill{left:46px;top:406px;width:609px;height:60px;font-size:34px}
</style>
</head>
<body>

<svg width="0" height="0" style="position:absolute" aria-hidden="true">
  <defs>
    <linearGradient id="star-fill" x1="0" y1="0" x2="1" y2="1">
      <stop offset="0" stop-color="#b9e0f7"/>
      <stop offset=".5" stop-color="#5fb0e6"/>
      <stop offset="1" stop-color="#2a86cc"/>
    </linearGradient>
    <linearGradient id="panel-blue" x1="0" y1="0" x2="0" y2="1">
      <stop offset="0" stop-color="#1d7ec3"/>
      <stop offset=".55" stop-color="#4a9fd8"/>
      <stop offset="1" stop-color="#93d6f3"/>
    </linearGradient>
    <linearGradient id="swoosh-fill" x1="0" y1="0" x2="1" y2="0">
      <stop offset="0" stop-color="#1d7ec3"/>
      <stop offset="1" stop-color="#9fd3f2"/>
    </linearGradient>
    <symbol id="star" viewBox="-1 -1 2 1.81">
      <polygon points="0,-1 0.2245,-0.309 0.951,-0.309 0.363,0.118 0.588,0.809 0,0.382 -0.588,0.809 -0.363,0.118 -0.951,-0.309 -0.2245,-0.309"
        fill="url(#star-fill)" stroke="#ffffff" stroke-width="0.04"/>
    </symbol>
    <symbol id="star-row" viewBox="0 0 300 90">
      <use href="#star" x="2" y="38" width="56" height="51"/>
      <use href="#star" x="242" y="38" width="56" height="51"/>
      <use href="#star" x="47" y="20" width="76" height="69"/>
      <use href="#star" x="177" y="20" width="76" height="69"/>
      <use href="#star" x="104" y="5" width="92" height="84"/>
    </symbol>
    <symbol id="icon-tag" viewBox="0 0 40 44">
      <path d="M4 6 L20 4 L36 20 L22 38 L6 22 Z"/>
      <circle cx="12" cy="11" r="2.5"/>
      <path d="M16 24 L26 16 M19 28 L28 21"/>
    </symbol>
    <symbol id="icon-cash" viewBox="0 0 40 44">
      <rect x="6" y="4" width="20" height="30" rx="2"/>
      <circle cx="16" cy="19" r="5"/>
      <path d="M20 40 L20 30 Q24 26 28 30 L34 36 L34 42"/>
    </symbol>
    <symbol id="icon-shield" viewBox="0 0 40 44">
      <path d="M20 3 L35 9 L35 22 Q35 35 20 41 Q5 35 5 22 L5 9 Z"/>
      <path d="M13 22 L18 27 L27 16"/>
    </symbol>
  </defs>
</svg>

<!-- Wide format -->
<section class="ad ad-wide" aria-label="Anzeige Querformat">
  <svg class="backdrop" viewBox="0 0 100 100" preserveAspectRatio="none" aria-hidden="true">
    <path d="M0 36 C30 30 62 22 100 30 L100 100 L0 100 Z" fill="url(#panel-blue)"/>
    <path d="M0 22 C4 32 14 35 26 34 C12 36 4 38 0 40 Z" fill="url(#swoosh-fill)"/>
    <path d="M55 26 C75 22 92 22 100 22 L100 30 C88 26 72 24 55 26 Z" fill="#9fd3f2"/>
  </svg>
  <div class="brand"><span class="brand-dot"></span><span class="brand-name">kalvimo.de</span></div>
  <svg class="stars" aria-hidden="true"><use href="#star-row" width="100%" height="100%"/></svg>
  <h2 class="headline">Traktor <span class="accent">Bewertung</span></h2>
  <div class="tractor-photo" role="img" aria-label="Foto eines blauen Oldtimer-Traktors"></div>
  <div class="services">
    <span class="lead">Kurzgutachen für</span>
    <div class="service"><svg><use href="#icon-tag"/></svg>Verkauf,</div>
    <div class="service"><svg><use href="#icon-cash"/></svg>Kauf oder</div>
    <div class="service"><svg><use href="#icon-shield"/></svg>Versicherung</div>
  </div>
  <div class="url-pill">www.kalvimo.de/traktorwert</div>
</section>

<!-- Tall format -->
<section class="ad ad-tall" aria-label="Anzeige Hochformat">
  <svg class="backdrop" viewBox="0 0 100 100" preserveAspectRatio="none" aria-hidden="true">
    <path d="M0 35 C30 30 62 24 100 32 L100 100 L0 100 Z" fill="url(#panel-blue)"/>
    <path d="M0 21 C4 29 13 31 30 31 C14 33 4 35 0 37 Z" fill="url(#swoosh-fill)"/>
    <path d="M58 27 C76 24 92 24 100 25 L100 31 C88 28 74 26 58 27 Z" fill="#9fd3f2"/>
  </svg>
  <div class="brand"><span class="brand-dot"></span><span class="brand-name">kalvimo.de</span></div>
  <svg class="stars" aria-hidden="true"><use href="#star-row" width="100%" height="100%"/></svg>
  <h2 class="headline">Traktor <span class="accent">Bewertung</span></h2>
  <div class="tractor-photo" role="img" aria-label="Foto eines blauen Oldtimer-Traktors"></div>
  <div class="services">
    <span class="lead">Kurzgutachen für</span>
    <div class="service"><svg><use href="#icon-tag"/></svg>Verkauf,</div>
    <div class="service"><svg><use href="#icon-cash"/></svg>Kauf oder</div>
    <div class="service"><svg><use href="#icon-shield"/></svg>Versicherung</div>
  </div>
  <div class="url-pill">www.kalvimo.de/traktorwert</div>
</section>

<!-- Small format -->
<section class="ad ad-small" aria-label="Anzeige klein">
  <svg class="backdrop" viewBox="0 0 100 100" preserveAspectRatio="none" aria-hidden="true">
    <path d="M0 33 C30 28 62 22 100 30 L100 100 L0 100 Z" fill="url(#panel-blue)"/>
    <path d="M0 19 C4 28 14 30 28 29 C13 31 4 33 0 35 Z" fill="url(#swoosh-fill)"/>
    <path d="M56 25 C76 21 92 21 100 22 L100 29 C88 25 73 23 56 25 Z" fill="#9fd3f2"/>
  </svg>
  <div class="brand"><span class="brand-dot"></span><span class="brand-name">kalvimo.de</span></div>
  <svg class="stars" aria-hidden="true"><use href="#star-row" width="100%" height="100%"/></svg>
  <h2 class="headline">Traktor <span class="accent">Bewertung</span></h2>
  <div class="tractor-photo" role="img" aria-label="Foto eines blauen Oldtimer-Traktors"></div>
  <div class="services">
    <span class="lead">Kurzgutachen für</span>
    <div class="service"><svg><use href="#icon-tag"/></svg>Verkauf,</div>
    <div class="service"><svg><use href="#icon-cash"/></svg>Kauf oder</div>
    <div class="service"><svg><use href="#icon-shield"/></svg>Versicherung</div>
  </div>
  <div class="url-pill">www.kalvimo.de/traktorwert</div>
</section>

</body>
</html>
```